Tech business card design

We need an amazing business card design for our new business 'Pexla' a marketing tech startup based in Sydney, Australia. We provide an online marketplace for businesses to search and buy advertising media, connect with service providers and learn more about marketing. We wish to communicate 'cool tech', reliability and professionalism and design based around our logo.

Target Market(s)

Business Owners

Contact Information for Business Card

Name
Position
Email Address
Website
Phone Number

Font styles to use
Other font styles liked:
• Avenir & Avenir Next

Colors

Designer to choose colors to be used in the design.

```html
<!DOCTYPE html>
<html lang="en">
<head>
<meta charset="utf-8">
<title>Pexla business card</title>
<link rel="stylesheet" href="https://fonts.googleapis.com/css2?family=Mulish:wght@400;800;900&display=swap">
<style>
  :root {
    --navy: #1b1a4d;
    --navy-deep: #141339;
    --ink-grey: #7a7a80;
    --rule: #55555c;
    --paper: #ffffff;
    --backdrop: #2a2a2d;
  }
  * { box-sizing: border-box; margin: 0; padding: 0; }
  html, body { width: 1200px; height: 892px; overflow: hidden; }
  body {
    background: var(--backdrop);
    font-family: "Mulish", sans-serif;
    display: flex;
    align-items: center;
    justify-content: center;
    gap: 40px;
  }
  .card {
    position: relative;
    width: 540px;
    height: 309px;
    overflow: hidden;
  }
  /* Back side */
  .card-back { background: var(--navy); }
  .card-back .brand-field {
    position: absolute; inset: 0;
    background: linear-gradient(135deg, #1f1d56 0%, #18174a 60%, #121138 100%);
  }
  .card-back .wordmark {
    position: absolute;
    right: 38px; bottom: 34px;
    color: var(--paper);
    font-weight: 900;
    font-size: 28px;
    letter-spacing: -0.5px;
  }
  /* Front side */
  .card-front { background: var(--paper); }
  .card-front .wordmark {
    position: absolute;
    right: 52px; top: 34px;
    color: var(--navy);
    font-weight: 900;
    font-size: 82px;
    letter-spacing: -2px;
    line-height: 1;
  }
  .card-front .trademark {
    position: absolute;
    right: 36px; top: 48px;
    color: var(--navy);
    font-weight: 800;
    font-size: 9px;
  }
  .divider {
    position: absolute;
    left: 40px; right: 36px; top: 186px;
    height: 1px;
    background: var(--rule);
  }
  .edge-tab {
    position: absolute;
    left: 0; top: 140px;
    width: 12px; height: 30px;
    background: var(--navy);
  }
  .person {
    position: absolute;
    left: 40px; top: 138px;
  }
  .person-name {
    color: var(--navy);
    font-weight: 800;
    font-size: 19px;
    line-height: 1.1;
  }
  .person-role {
    color: var(--ink-grey);
    font-size: 13px;
  }
  .contacts {
    position: absolute;
    left: 40px; top: 198px;
    list-style: none;
    color: var(--ink-grey);
    font-size: 13px;
  }
  .contacts li {
    display: flex; align-items: center; gap: 10px;
    height: 22px;
  }
  .contacts svg { width: 14px; height: 14px; flex: none; }
  .web-band {
    position: absolute;
    right: 0; bottom: 0;
    width: 240px; height: 34px;
  }
  .web-band svg { position: absolute; inset: 0; }
  .web-address {
    position: absolute;
    right: 20px; bottom: 9px;
    color: var(--paper);
    font-size: 12px;
    letter-spacing: 0.5px;
  }
</style>
</head>
<body>
  <section class="card card-back" aria-label="Card back">
    <div class="brand-field" role="img" aria-label="Faint repeating brand name pattern on navy"></div>
    <span class="wordmark">Pexla</span>
  </section>

  <section class="card card-front" aria-label="Card front">
    <span class="wordmark">Pexla</span>
    <span class="trademark">TM</span>

    <div class="edge-tab"></div>
    <div class="person">
      <p class="person-name">Marcus Dale</p>
      <p class="person-role">Founder, Director</p>
    </div>
    <div class="divider"></div>

    <ul class="contacts">
      <li>
        <svg viewBox="0 0 14 14" aria-hidden="true"><rect x="3.5" y="0.5" width="7" height="13" rx="1.2" fill="none" stroke="#1b1a4d" stroke-width="1.4"/><rect x="6" y="11" width="2" height="1.2" fill="#1b1a4d"/></svg>
        <span>+61 (0)412 555 208</span>
      </li>
      <li>
        <svg viewBox="0 0 14 14" aria-hidden="true"><rect x="0.5" y="3" width="13" height="9" fill="#1b1a4d"/><path d="M0.5 3 L7 8 L13.5 3" fill="none" stroke="#fff" stroke-width="1.2"/></svg>
        <span>marcus@pexlamedia.com.au</span>
      </li>
    </ul>

    <div class="web-band">
      <svg viewBox="0 0 240 34" preserveAspectRatio="none" aria-hidden="true"><polygon points="14,0 240,0 240,34 0,34" fill="#1b1a4d"/></svg>
      <span class="web-address">www.pexlamedia.com.au</span>
    </div>
  </section>
</body>
</html>
```